Web Design For Marlow Pool Service

We are working with a company that wants a website for their pool service. Some sites to use for content/competitors and inspiration:
https://sacramento.brightwaterpoolco.example/builder/newbuild/repair/ppc
https://hollowbrookpoolcareplus.example/
https://lakemontpoolservice.example/
https://www.dravenspoolresurfacing.example/pool-renovation-ga/
Thank you for taking the time to consider designing a website for us. We are web developers based in Stockton, CA, USA. Most of our projects go through the same process. Understanding this process may help you win a project with us. We custom-code all of our websites in-house. We don’t have any requirements as to what tools you use for your design, but we prefer Figma files. For any design that we label as four-stars, we send it to the client for review. The client picks the final design they want us to use. Once we complete this process, we will continue to show additional clients all the four-star sites and purchase them later. Your designs will have multiple chances to sell. For better chances of success, we ask that you follow these guidelines.
IMAGES:
If you use any images or icons in the design, we ask that you have a link to the asset so we can purchase the image/icon. Most of the designs we submit do not have the customer’s images on them unless they have some great images. Be creative; show us the feeling you are trying to portray with your image choices. Use any royalty-free site you choose. We subscribe to Adobe and mainly use their images, but we can purchase images outside of Adobe. PLEASE NOTE: we will not submit designs to clients with watermarks on the images.
FONTS:
We ask that you identify the fonts used in the design. This can be done in a message if you want. We typically use Google Fonts and Adobe Fonts.
CONTENT:
We're always open to different content and ideas. We often submit designs with stock images so the client can see our vision. We typically take pictures after the website launch to use their images with our vision. Lorem Ipsum is fine for paragraphs, but we ask that you write the headers in correct English. We want to be able to show the vision and identify the sections of the website.
INSPIRATION:
We typically add a couple of links in the brief of websites we like to help you get started in your design.
REVISIONS:
We do not often ask for revisions of the designs unless we see something in the design that may not appeal to the client. If there are slight changes that we want to make, we do that in the development process.
FEEDBACK:
We rarely give feedback on designs during the design process. We are working on many website projects and do not have the time to provide feedback. We usually respond if your request is well thought out and asks specific questions, but a note asking “feedback, please” usually goes unanswered.
Number of Pages Required
1 page
Look and feel
Each slider illustrates characteristics of the customer's brand and the style your logo design should communicate.

```html
<!DOCTYPE html>
<html lang="en">
<head>
<meta charset="utf-8">
<title>Marlow Pool Service</title>
<link href="https://fonts.googleapis.com/css2?family=Fira+Sans:wght@500;600&family=Open+Sans:wght@400;600;700&display=swap" rel="stylesheet">
<style>
:root{
  --navy:#1a3f73;
  --navy-deep:#133257;
  --blue:#2196f3;
  --ink:#333a44;
  --muted:#6c7480;
  --panel:#eef3f6;
  --soft:#f4f7fb;
  --white:#ffffff;
}
*{box-sizing:border-box;margin:0;padding:0}
html,body{width:1200px;height:3825px;overflow:hidden}
body{position:relative;background:var(--white);font-family:"Open Sans",Arial,sans-serif;color:var(--ink)}
.abs{position:absolute}
h1,h2,h3{font-family:"Fira Sans",Arial,sans-serif;font-weight:600}

/* header */
.site-header{left:0;top:0;width:1200px;height:67px;background:var(--white)}
.brand{left:104px;top:14px;display:flex;align-items:center;gap:8px;color:var(--blue);font-weight:600;font-size:17px;letter-spacing:.5px}
.brand-dot{width:14px;height:14px;border-radius:50%;background:var(--blue)}
.main-nav{left:353px;top:24px;display:flex;gap:0;font-size:14px;font-weight:700;color:var(--ink)}
.main-nav a{color:inherit;text-decoration:none;position:absolute;white-space:nowrap}
.quote-btn{left:888px;top:0;width:312px;height:67px;background:var(--navy);color:var(--white);font-size:14px;font-weight:700;display:flex;align-items:center;padding-left:40px;gap:40px}

/* hero */
.hero{left:0;top:67px;width:1200px;height:574px;background:linear-gradient(180deg,#7c8a8e 0%,#9d9284 45%,#8b7660 75%,#6f5c49 100%)}
.hero-box{left:89px;top:230px;width:576px;height:302px;background:rgba(40,40,40,.72)}
.hero-box .bar{position:absolute;left:0;top:42px;width:4px;height:82px;background:var(--blue)}
.hero-box h1{position:absolute;left:29px;top:36px;color:var(--white);font-size:38px;line-height:54px;letter-spacing:.5px}
.hero-box p{position:absolute;left:29px;top:148px;width:500px;color:#f0f0f0;font-size:14px;line-height:29px}
.btn{display:inline-flex;align-items:center;justify-content:center;background:var(--blue);color:var(--white);font-weight:700;font-size:14px;text-decoration:none}
.hero-box .btn{position:absolute;left:28px;top:225px;width:198px;height:43px}

/* features */
.feature{top:735px;width:310px;display:flex;gap:10px}
.feature .icon{flex:none;width:53px;height:53px;border-radius:50%;background:var(--navy);display:flex;align-items:center;justify-content:center}
.feature h3{font-family:"Open Sans",Arial,sans-serif;font-weight:700;font-size:15px;color:var(--ink);margin-top:1px}
.feature p{font-size:12px;line-height:15px;color:var(--ink);width:240px}

/* about */
.about-panel{left:267px;top:940px;width:933px;height:408px;background:var(--panel);border-bottom-left-radius:70px}
.about-frame{left:144px;top:924px;width:364px;height:372px;border:4px solid var(--blue);border-radius:4px}
.about-photo{left:125px;top:903px;width:365px;height:374px;background:linear-gradient(135deg,#2a9ed8 0%,#6fc3e8 35%,#c9cdd0 60%,#8e949a 100%)}
.eyebrow{font-size:13px;color:var(--ink);letter-spacing:.3px}
.about-text{left:563px;top:980px;width:510px}
.about-text h2{font-size:35px;color:var(--navy);margin:6px 0 14px}
.about-text p{font-size:13.5px;line-height:23.7px;color:var(--muted);margin-bottom:5px}

/* section titles */
.section-label{left:0;width:1200px;display:flex;justify-content:center;align-items:center;gap:22px;font-size:12px;font-weight:700;color:var(--blue)}
.section-label::before,.section-label::after{content:"";width:48px;height:2px;background:var(--blue)}
.section-title{left:0;width:1200px;text-align:center;font-size:45px;color:var(--navy)}

/* services */
.services-bg{left:0;top:1400px;width:1200px;height:560px;background:linear-gradient(180deg,#ffffff 0%,#eef5fb 100%)}
.service-card{top:1579px;width:301px;height:245px;background:var(--white);border-radius:6px;box-shadow:0 3px 12px rgba(20,50,90,.1);overflow:hidden}
.service-card .photo{height:143px}
.service-card h3{display:flex;align-items:center;gap:8px;margin:14px 0 8px 17px;font-size:18px;font-weight:500;color:var(--navy)}
.service-card p{margin-left:17px;width:260px;font-size:12.5px;line-height:16px;color:var(--ink)}

/* banner */
.banner{left:0;top:1938px;width:1200px;height:356px}
.banner-text{left:0;top:2012px;width:1200px;text-align:center;color:var(--white)}
.banner-text h2{font-size:40px;line-height:46px}
.banner-text p{font-size:20px;margin-top:12px}
.banner .btn{}
.pill{left:509px;top:2173px;width:180px;height:41px;border-radius:21px;font-weight:400;font-size:15px;gap:8px}

/* testimonials */
.review{top:2487px;width:322px;height:176px;background:#f4f4f4;text-align:center;font-size:12.5px;line-height:23px;color:var(--muted);padding:40px 48px 0}
.review.active{background:var(--navy);color:var(--white)}
.review .tip{position:absolute;left:138px;bottom:-22px;width:0;height:0;border-left:23px solid transparent;border-right:23px solid transparent;border-top:22px solid var(--navy)}
.person{top:2696px;width:140px;text-align:center}
.person .avatar{width:46px;height:46px;border-radius:50%;margin:0 auto 6px;background:linear-gradient(160deg,#c9b39b,#6b7685)}
.person b{display:block;font-size:9px;color:var(--ink)}
.person span{font-size:8.5px;color:var(--muted)}

/* contact */
.contact-bg{left:0;top:2847px;width:1200px;height:540px;background:var(--soft)}
.contact-card{top:3032px;width:301px;height:243px;background:var(--white);text-align:center;padding-top:38px}
.contact-card h3{font-family:"Open Sans",Arial,sans-serif;font-weight:400;font-size:15px;color:#111;margin-top:14px}
.contact-card .line-blue{color:var(--blue);font-size:14px;margin-top:8px}
.contact-card .line{color:#111;font-size:14px;margin-top:2px}
.contact-card .link{display:inline-flex;gap:10px;align-items:center;margin-top:18px;font-size:12px;color:var(--blue);border-bottom:1.5px solid var(--blue);padding-bottom:3px}

/* footer */
.footer-wave{left:0;top:3330px;width:1200px;height:495px}
.footer-brand{left:0;top:3515px;width:1200px;display:flex;justify-content:center;align-items:center;gap:12px;color:var(--blue);font-size:34px;font-weight:600;letter-spacing:1px}
.footer-brand .dot{width:22px;height:22px;border-radius:50%;background:var(--blue)}
.footer-col h4{font-size:15px;font-weight:700;color:var(--white)}
.footer-col .row{display:flex;gap:16px;align-items:flex-start;color:var(--white);font-size:12px;line-height:21px}
.footer-about{left:450px;top:3608px;width:300px;text-align:center;color:var(--white);font-size:12px;line-height:21px}
.social{top:3697px;width:36px;height:34px;border:1.5px solid var(--white)}
.hours{left:880px;top:3561px;width:226px;text-align:right}
.hours .row{justify-content:flex-end;margin-top:14px}
.divider{left:62px;top:3775px;width:1076px;height:1px;background:rgba(255,255,255,.35)}
.copyright{left:0;top:3791px;width:1200px;text-align:center;color:var(--white);font-size:12px}
</style>
</head>
<body>

<header class="abs site-header">
  <div class="abs brand"><span class="brand-dot"></span>Marlow Pool Service</div>
  <nav class="abs main-nav">
    <a style="left:0">HOME</a>
    <a style="left:103px">ABOUT US</a>
    <a style="left:244px">SERVICES</a>
    <a style="left:370px">CONTACT US</a>
  </nav>
  <a class="abs quote-btn">
    <svg width="12" height="18" viewBox="0 0 12 18"><path d="M2 2l7 7-7 7" fill="none" stroke="#fff" stroke-width="2"/></svg>
    GET QUOTATION
  </a>
</header>

<section class="abs hero" role="img" aria-label="Children running toward a backyard swimming pool on a sunny afternoon"></section>
<div class="abs hero-box">
  <span class="bar"></span>
  <h1>Crafting Memories,<br>One Pool at a Time</h1>
  <p>It is a long and established fact that a reader will be distracted by the readable content of a page when looking.</p>
  <a class="btn">REQUEST A DEMO</a>
</div>

<div class="abs feature" style="left:126px">
  <span class="icon"><svg width="22" height="22" viewBox="0 0 24 24" fill="none" stroke="#fff" stroke-width="1.6"><circle cx="12" cy="12" r="3.5"/><path d="M12 2l2 3 3.5-.5.5 3.5 3 2-3 2-.5 3.5-3.5-.5-2 3-2-3-3.5.5L6 15.5 3 13.5l3-2L6.5 8 10 8.5z"/></svg></span>
  <div><h3>Expertise</h3><p>Lorem ipsum dolor sit amet, consectetur adipiscing elit, sed do eiusmod</p></div>
</div>
<div class="abs feature" style="left:450px">
  <span class="icon"><svg width="22" height="22" viewBox="0 0 24 24" fill="none" stroke="#fff" stroke-width="1.6"><circle cx="12" cy="12" r="8"/><path d="M4 12h16M12 4c3 3 3 13 0 16M12 4c-3 3-3 13 0 16"/></svg></span>
  <div><h3>Professional</h3><p>Lorem ipsum dolor sit amet, consectetur adipiscing elit, sed do eiusmod</p></div>
</div>
<div class="abs feature" style="left:774px">
  <span class="icon"><svg width="22" height="22" viewBox="0 0 24 24" fill="none" stroke="#fff" stroke-width="1.6"><circle cx="12" cy="8" r="3.5"/><path d="M5 20c0-4 3-6 7-6s7 2 7 6z"/></svg></span>
  <div><h3>Experienced</h3><p>Lorem ipsum dolor sit amet, consectetur adipiscing elit, sed do eiusmod</p></div>
</div>

<div class="abs about-panel"></div>
<div class="abs about-frame"></div>
<div class="abs about-photo" role="img" aria-label="Technician with a toolbox servicing equipment beside a pool deck"></div>
<div class="abs about-text">
  <div class="eyebrow">ABOUT US</div>
  <h2>Making Waves with Excellence</h2>
  <p>Lorem ipsum dolor sit amet, consectetur adipiscing elit, sed do eiusmod tempor incididunt ut labore et dolore magna aliqua. Ut enim ad minim veniam, quis nostrud exercitation ullamco laboris nisi ut aliquip ex ea commodo consequat. Duis aute irure dolor in reprehenderit in voluptate velit esse cillum dolore eu fugiat nulla pariatur. Excepteur sint occaecat cupidatat non proident, sunt in culpa qui officia deserunt mollit anim id est laborum.</p>
  <p>Lorem ipsum dolor sit amet, consectetur adipiscing elit, sed do eiusmod tempor incididunt ut labore et dolore magna aliqua. Ut enim ad minim veniam, quis nostrud exercitation ullamco laboris nisi ut aliquip ex ea commodo consequat. Duis aute irure dolor in reprehenderit</p>
</div>

<div class="abs services-bg"></div>
<div class="abs section-label" style="top:1446px">SERVICES</div>
<h2 class="abs section-title" style="top:1470px">Services We Provide</h2>

<article class="abs service-card" style="left:125px">
  <div class="photo" role="img" aria-label="Worker cleaning blue pool tiles" style="background:linear-gradient(135deg,#3d8fc4,#8cc3e0 60%,#2f5f86)"></div>
  <h3><svg width="18" height="18" viewBox="0 0 18 18"><circle cx="9" cy="9" r="9" fill="#6c7480"/><path d="M5 9l3 3 5-6" fill="none" stroke="#fff" stroke-width="2"/></svg>Pool Repair</h3>
  <p>Lorem ipsum is simply dummy text of the printing and typesetting...</p>
</article>
<article class="abs service-card" style="left:450px">
  <div class="photo" role="img" aria-label="Construction crew in hard hats on a building site" style="background:linear-gradient(135deg,#cfd6dc,#e9ecee 50%,#9aa8b3)"></div>
  <h3><svg width="18" height="18" viewBox="0 0 18 18"><circle cx="9" cy="9" r="9" fill="#6c7480"/><path d="M5 9l3 3 5-6" fill="none" stroke="#fff" stroke-width="2"/></svg>Pool Construction</h3>
  <p>Lorem ipsum is simply dummy text of the printing and typesetting...</p>
</article>
<article class="abs service-card" style="left:772px">
  <div class="photo" role="img" aria-label="Family relaxing on a float in a clear pool" style="background:linear-gradient(135deg,#3fb6c9,#7fd6dc 55%,#b9855e)"></div>
  <h3><svg width="18" height="18" viewBox="0 0 18 18"><circle cx="9" cy="9" r="9" fill="#6c7480"/><path d="M5 9l3 3 5-6" fill="none" stroke="#fff" stroke-width="2"/></svg>Pool Cleaning</h3>
  <p>Lorem ipsum is simply dummy text of the printing and typesetting...</p>
</article>

<svg class="abs banner" viewBox="0 0 1200 356" role="img" aria-label="Modern home with a lit pool at dusk">
  <defs><linearGradient id="dusk" x1="0" y1="0" x2="0" y2="1"><stop offset="0" stop-color="#4a4f5c"/><stop offset=".55" stop-color="#2c3444"/><stop offset="1" stop-color="#1c3550"/></linearGradient></defs>
  <path d="M0 40 Q600 -40 1200 40 L1200 310 Q600 400 0 310 Z" fill="url(#dusk)"/>
</svg>
<div class="abs banner-text">
  <h2>Inspired Designs,<br>Impeccable Craftsmanship</h2>
  <p>Get in touch with us for the best experienced professional services</p>
</div>
<a class="abs btn pill">CONTACT US <svg width="14" height="12" viewBox="0 0 14 12"><path d="M1 6h11M7 1l5 5-5 5" fill="none" stroke="#fff" stroke-width="1.5"/></svg></a>

<div class="abs section-label" style="top:2370px">TESTIMONIALS</div>
<h2 class="abs section-title" style="top:2394px">Client Reviews</h2>

<div class="abs review" style="left:92px">Lorem ipsum dolor sit amet, consectetur adipiscing elit, sed do eiusmod tempor incididunt ut labore et dolore magna aliqua.<span class="tip"></span></div>
<div class="abs review active" style="left:438px">Lorem ipsum dolor sit amet, consectetur adipiscing elit, sed do eiusmod tempor incididunt ut labore et dolore magna aliqua.<span class="tip"></span></div>
<div class="abs review" style="left:786px">Lorem ipsum dolor sit amet, consectetur adipiscing elit, sed do eiusmod tempor incididunt ut labore et dolore magna aliqua.<span class="tip"></span></div>

<div class="abs person" style="left:183px"><div class="avatar" role="img" aria-label="Customer portrait"></div><b>Dana Whitfield</b><span>Customer</span></div>
<div class="abs person" style="left:528px"><div class="avatar" role="img" aria-label="Customer portrait"></div><b>Dana Whitfield</b><span>Customer</span></div>
<div class="abs person" style="left:876px"><div class="avatar" role="img" aria-label="Customer portrait"></div><b>Dana Whitfield</b><span>Customer</span></div>

<div class="abs contact-bg"></div>
<div class="abs section-label" style="top:2910px">CONTACT US</div>
<h2 class="abs section-title" style="top:2934px">Get in touch with us</h2>

<div class="abs contact-card" style="left:131px">
  <svg width="44" height="40" viewBox="0 0 44 40" fill="none" stroke="#2196f3" stroke-width="1.6"><path d="M22 28s-9-9-9-15a9 9 0 0118 0c0 6-9 15-9 15z"/><circle cx="22" cy="13" r="3.5"/><path d="M10 26l-6 12h36l-6-12"/></svg>
  <h3>FIND US</h3>
  <div class="line-blue">Elm Avenue</div>
  <div class="line">City, District, Country</div>
  <span class="link">CONTACT US <svg width="12" height="10" viewBox="0 0 12 10"><path d="M1 5h9M6 1l4 4-4 4" stroke="#2196f3" fill="none" stroke-width="1.4"/></svg></span>
</div>
<div class="abs contact-card" style="left:456px">
  <svg width="44" height="40" viewBox="0 0 44 40" fill="none" stroke="#2196f3" stroke-width="1.6"><path d="M12 4l6 0 3 8-4 3c2 4 5 7 9 9l3-4 8 3v6c0 2-2 3-4 3C20 32 10 22 10 8c0-2 1-4 2-4z"/></svg>
  <h3>CALL US AT</h3>
  <div class="line-blue">(123) 456-7890</div>
  <div class="line">info@marlowpool.example</div>
  <span class="link">CONTACT US <svg width="12" height="10" viewBox="0 0 12 10"><path d="M1 5h9M6 1l4 4-4 4" stroke="#2196f3" fill="none" stroke-width="1.4"/></svg></span>
</div>
<div class="abs contact-card" style="left:781px">
  <svg width="44" height="40" viewBox="0 0 44 40" fill="none" stroke="#2196f3" stroke-width="1.6"><path d="M6 14l16-11 16 11v22H6z"/><path d="M6 14l16 12 16-12"/><circle cx="22" cy="14" r="4"/></svg>
  <h3>EMAIL US</h3>
  <div class="line-blue">(123) 456-7890</div>
  <div class="line">info@marlowpool.example</div>
  <span class="link">CONTACT US <svg width="12" height="10" viewBox="0 0 12 10"><path d="M1 5h9M6 1l4 4-4 4" stroke="#2196f3" fill="none" stroke-width="1.4"/></svg></span>
</div>

<svg class="abs footer-wave" viewBox="0 0 1200 495" preserveAspectRatio="none">
  <path d="M0 110 Q300 40 600 20 Q900 10 1200 70 L1200 495 L0 495 Z" fill="#d6e9f5"/>
  <path d="M0 105 Q300 55 600 62 Q900 60 1200 100 L1200 495 L0 495 Z" fill="#9fcde9"/>
  <path d="M0 112 Q400 80 700 78 Q1000 80 1200 118 L1200 495 L0 495 Z" fill="#133257"/>
</svg>

<div class="abs footer-brand"><span class="dot"></span>Marlow Pool Service</div>

<div class="abs footer-col" style="left:92px;top:3561px;width:260px">
  <h4>CONTACT US</h4>
  <div class="row" style="margin-top:18px"><svg width="16" height="20" viewBox="0 0 16 20"><path d="M8 19s-7-7-7-12a7 7 0 0114 0c0 5-7 12-7 12z" fill="#fff"/><circle cx="8" cy="7" r="2.5" fill="#133257"/></svg><span>101- lorem ipsum simple text<br>print type text industry text.</span></div>
  <div class="row" style="margin-top:12px"><svg width="16" height="16" viewBox="0 0 16 16"><path d="M3 1h3l1.5 4-2 1.5c1 2 2.5 3.5 4.5 4.5L11.5 9l4 1.5v3c0 1-1 1.5-2 1.5C7 15 1 9 1 3c0-1 1-2 2-2z" fill="#fff"/></svg><span>123 456 7890</span></div>
  <div class="row" style="margin-top:14px"><svg width="16" height="12" viewBox="0 0 16 12"><rect width="16" height="12" fill="#fff"/><path d="M0 0l8 7 8-7" fill="none" stroke="#133257" stroke-width="1.4"/></svg><span>info@marlowpool.example</span></div>
</div>

<p class="abs footer-about">Lorem ipsum dolor sit amet, consectetur adipiscing elit, sed do eiusmod tempor incididunt bbbbbut bcbbcbnmx zjzmsmmzm</p>
<span class="abs social" style="left:536px"></span>
<span class="abs social" style="left:582px"></span>
<span class="abs social" style="left:626px"></span>

<div class="abs footer-col hours">
  <h4>OPENING HOURS</h4>
  <div class="row" style="margin-top:22px">Mon - Fri: 9am - to - 6pm <svg width="16" height="16" viewBox="0 0 16 16" fill="none" stroke="#fff" stroke-width="1.4"><circle cx="8" cy="8" r="7"/><path d="M8 4v4h3"/></svg></div>
  <div class="row">Saturday 9am - to - 2pm <svg width="16" height="16" viewBox="0 0 16 16" fill="none" stroke="#fff" stroke-width="1.4"><circle cx="8" cy="8" r="7"/><path d="M8 4v4h3"/></svg></div>
  <div class="row">Sunday : <u>Closed</u> <svg width="16" height="16" viewBox="0 0 16 16" fill="none" stroke="#fff" stroke-width="1.4"><circle cx="8" cy="8" r="7"/><path d="M8 4v4h3"/></svg></div>
</div>

<div class="abs divider"></div>
<div class="abs copyright">Marlow Pool Service</div>

</body>
</html>
```